Business Card Design

I'm a commercial general contractor remodel offices, hotels, health clubs and stores mostly San Francisco and the peninsula
the file I down loaded is kind of what I want I like the I beam with my company name in it, that would be fine with me but if you have better Idea will look at it you never know, I'm decided to give in and change my company name to how every one knows me, I have been in business since 1991, I like the I beam logo I included one of my old card from my old company for reference for you.

BROCK CONSTRUCTION (is my company name)
Warren Pelkey contractor, LIc 514387
3148 Larkspur Row, San Bruno, California 94071
mobile, (415) 736-4052
phone (650) 514-2087
Fax, (650) 514-2088
email, brock@brockconstruction.example

```html
<!DOCTYPE html>
<html lang="en">
<head>
<meta charset="utf-8">
<title>Brock Construction — Business Card</title>
<link rel="stylesheet" href="https://fonts.googleapis.com/css2?family=Arimo:wght@400;700&family=Tinos:wght@400;700&display=swap">
<style>
  :root {
    --page-bg: #ececec;
    --card-paper: #f5f3ee;
    --brand-blue: #2a86cc;
    --brand-blue-dark: #1c6fb0;
    --mark-tint: #9fc7e8;
    --ink: #1e1e1e;
    --ink-soft: #5a5a5a;
    --white: #ffffff;
  }
  * { margin: 0; padding: 0; box-sizing: border-box; }
  html, body {
    width: 1200px;
    height: 900px;
    overflow: hidden;
    background: var(--page-bg);
    font-family: "Arimo", Arial, sans-serif;
  }
  .business-card {
    position: absolute;
    left: 180px;
    top: 210px;
    width: 840px;
    height: 480px;
    background: var(--card-paper);
    overflow: hidden;
  }
  .blue-panel {
    position: absolute;
    left: 353px;
    top: 0;
    right: 0;
    bottom: 0;
    background: var(--brand-blue);
  }
  .brand-mark {
    position: absolute;
    left: 40px;
    top: 50px;
    display: flex;
    align-items: center;
    gap: 10px;
  }
  .brand-mark__square {
    width: 26px;
    height: 26px;
    background: var(--mark-tint);
  }
  .brand-mark__name {
    font-weight: 700;
    font-size: 22px;
    color: var(--brand-blue);
    white-space: nowrap;
  }
  .company-banner {
    position: absolute;
    left: 110px;
    top: 132px;
    width: 580px;
    height: 62px;
    background: var(--white);
    border: 2px solid var(--brand-blue-dark);
    display: flex;
    align-items: center;
    justify-content: center;
    font-family: "Tinos", "Times New Roman", serif;
    font-weight: 400;
    font-size: 30px;
    letter-spacing: 1px;
    color: var(--brand-blue);
    white-space: nowrap;
  }
  .license {
    position: absolute;
    right: 40px;
    top: 30px;
    font-size: 13px;
    color: var(--white);
  }
  .person {
    position: absolute;
    left: 40px;
    top: 252px;
  }
  .person__name {
    font-size: 24px;
    color: var(--brand-blue);
    letter-spacing: 0.5px;
    text-transform: uppercase;
  }
  .person__title {
    font-size: 15px;
    color: var(--ink-soft);
    margin-top: 2px;
  }
  .contact-left {
    position: absolute;
    left: 40px;
    top: 336px;
    font-size: 15px;
    font-style: normal;
    line-height: 1.45;
    color: var(--ink);
  }
  .contact-right {
    position: absolute;
    right: 40px;
    top: 232px;
    text-align: right;
    font-size: 15px;
    line-height: 1.55;
    color: var(--white);
  }
  .website {
    position: absolute;
    right: 40px;
    top: 330px;
    font-size: 15px;
    color: var(--ink);
  }
</style>
</head>
<body>
  <article class="business-card">
    <div class="blue-panel"></div>

    <div class="brand-mark">
      <span class="brand-mark__square"></span>
      <span class="brand-mark__name">BROCK CONSTRUCTION</span>
    </div>

    <p class="license">Lic #514387</p>

    <h1 class="company-banner">BROCK CONSTRUCTION</h1>

    <div class="person">
      <p class="person__name">Warren Pelkey</p>
      <p class="person__title">President</p>
    </div>

    <address class="contact-left">
      Email : brock@brockconstruction.example<br>
      3148 Larkspur Row<br>
      San Bruno, Ca 94071
    </address>

    <p class="contact-right">
      Telephone (650) 514-2087<br>
      Fax (650) 514-2088<br>
      Cell (415) 736-4052
    </p>

    <p class="website">www.brockconstruction.example</p>
  </article>
</body>
</html>
```